Executive Performance Review mapped on J-curve

I need to turn an executive company performance review into a visual infographic. The list of accomplishments is grouped into four calendar quarters. Each quarter needs a subtle representation of the season. The four quarters and associated list of accomplishments need to be mapped to a J-curve. - Spreadsheet with accomplishments attached (Marlowbend)- Sample image of a J-curve. You can google J-curve to see more images.- The title should be "Danica Ostrander Year in Review"

Target Market(s)

Board of Directors

Requirements
Nice to have
• This will be presented to a company founder that is an artist and customer experience expert. He is very visual so a nice visual representation of the data will be impactful. He also uses the phrase that you have to live with or work with someone for four seasons before you really know them. This is why I have the seasons mapped to the quarters. The Fall season motif should be gloomy and stormy.

```html
<!DOCTYPE html>
<html lang="en">
<head>
<meta charset="utf-8">
<title>Danica Ostrander – Year in Review</title>
<link href="https://fonts.googleapis.com/css2?family=Bebas+Neue&family=Fira+Sans:wght@400;500;600&family=Montserrat:wght@300&display=swap" rel="stylesheet">
<style>
:root{
  --bg:#f7f7f7;
  --frame:#c9c9c9;
  --ink:#555;
  --title:#7a7a7a;
  --summer:#f2cf4a;
  --summer-text:#e3b420;
  --fall:#aeaeae;
  --fall-text:#8c8c8c;
  --winter:#29a7df;
  --spring:#f47f7e;
}
*{box-sizing:border-box;margin:0;padding:0}
html,body{width:1041px;height:1200px;overflow:hidden}
body{
  position:relative;
  background:radial-gradient(circle at 50% 48%,#fff 0,#fbfbfb 30%,var(--bg) 70%);
  font-family:"Fira Sans",sans-serif;color:var(--ink);
}
.frame{position:absolute;left:41px;top:41px;width:957px;height:1124px;border:2px solid var(--frame);border-top:none}
.frame-top{position:absolute;top:41px;height:2px;background:var(--frame)}
.frame-top.left{left:41px;width:255px}
.frame-top.right{left:770px;width:228px}
.owner{position:absolute;top:24px;left:0;width:1041px;text-align:center;font-family:"Montserrat",sans-serif;font-weight:300;font-size:23px;letter-spacing:7px;color:var(--title)}
.headline{position:absolute;top:60px;left:0;width:1041px;text-align:center;font-family:"Bebas Neue",sans-serif;font-size:62px;letter-spacing:5px;color:var(--title);line-height:1}
.curve{position:absolute;left:0;top:0;width:1041px;height:697px}
.curve text{font-family:"Bebas Neue",sans-serif}
.phase-row{position:absolute;left:0;top:707px;width:1041px;height:34px}
.pill{position:absolute;top:0;height:31px;border-radius:16px;color:#fff;font-family:"Bebas Neue",sans-serif;font-size:22px;line-height:32px;padding-left:42px;box-shadow:3px 4px 6px rgba(0,0,0,.12)}
.pill svg{position:absolute;left:12px;top:5px}
.pill.assessment{left:132px;width:149px;background:var(--summer)}
.pill.stabilize{left:358px;width:124px;background:var(--fall)}
.pill.stratactical{left:555px;width:151px;background:var(--winter)}
.pill.strategic{left:780px;width:129px;background:var(--spring)}
.column{position:absolute;top:762px;width:215px;font-size:9.4px;line-height:12.4px}
.column.assessment{left:86px}.column.stabilize{left:310px}.column.stratactical{left:533px}.column.strategic{left:757px}
.column h3{font-size:9.6px;font-weight:600;line-height:12.4px}
.column h3.effectiveness{margin-top:12.4px}
.assessment h3{color:var(--summer-text)}.stabilize h3{color:#777}.stratactical h3{color:var(--winter)}.strategic h3{color:var(--spring)}
.group{list-style:none}
.group>li>span{display:block;padding-left:15px;position:relative;font-weight:500}
.group>li>span::before{content:"";position:absolute;left:4px;top:3px;border-left:6px solid var(--mark);border-top:3.5px solid transparent;border-bottom:3.5px solid transparent}
.items{list-style:none}
.items li{padding-left:44px;text-indent:-15px;position:relative}
.items li::before{content:"✓";display:inline-block;width:15px;text-indent:0;color:var(--mark);font-weight:600}
.assessment{--mark:var(--summer)}.stabilize{--mark:var(--fall)}.stratactical{--mark:var(--winter)}.strategic{--mark:var(--spring)}
</style>
</head>
<body>
<div class="frame"></div>
<div class="frame-top left"></div>
<div class="frame-top right"></div>
<div class="owner">DANICA OSTRANDER</div>
<div class="headline">YEAR IN REVIEW</div>

<svg class="curve" viewBox="0 0 1792 1200" aria-label="J-curve of four seasonal quarters leading to 2020 value creation">
  <!-- curve segments -->
  <path d="M530 778 Q560 905 690 918" fill="none" stroke="var(--summer)" stroke-width="30" stroke-linecap="round"/>
  <path d="M690 918 Q840 890 947 771" fill="none" stroke="var(--fall)" stroke-width="30" stroke-linecap="round"/>
  <path d="M947 771 L1120 569" fill="none" stroke="var(--winter)" stroke-width="30" stroke-linecap="round"/>
  <path d="M1120 569 L1270 390" fill="none" stroke="var(--spring)" stroke-width="30" stroke-linecap="round"/>

  <!-- summer -->
  <g stroke="var(--summer)" fill="none" stroke-width="3">
    <path d="M255 778 H487 A44 44 0 0 1 574 778"/>
  </g>
  <circle cx="256" cy="778" r="9" fill="var(--summer)"/>
  <circle cx="530" cy="778" r="26" fill="var(--summer)"/><circle cx="530" cy="778" r="11" fill="#fff"/>
  <g fill="var(--summer)">
    <circle cx="205" cy="773" r="24"/>
    <g stroke="var(--summer)" stroke-width="8" stroke-linecap="round">
      <path d="M205 738v8M205 800v8M170 773h8M232 773h8M180 748l6 6M224 792l6 6M230 748l-6 6M186 792l-6 6"/>
    </g>
    <circle cx="205" cy="773" r="15" fill="none" stroke="#fff" stroke-width="3"/>
  </g>
  <text x="297" y="763" font-size="34" fill="var(--summer)">SUMMER</text>
  <text x="297" y="831" font-size="60" fill="var(--summer)">Q3 2018</text>

  <!-- fall -->
  <path d="M655 942 A44 44 0 0 0 727 942" fill="none" stroke="var(--fall)" stroke-width="3"/>
  <path d="M690 960 V1010 Q690 1027 673 1027 H440" fill="none" stroke="var(--fall)" stroke-width="3"/>
  <circle cx="439" cy="1027" r="9" fill="var(--fall)"/>
  <circle cx="690" cy="918" r="26" fill="var(--fall)"/><circle cx="690" cy="918" r="11" fill="#fff"/>
  <path d="M390 998 L402 1012 L418 1008 L410 1026 L420 1038 L400 1040 L394 1058 L388 1040 L366 1040 L376 1026 L364 1008 L380 1012 Z" fill="var(--fall)"/>
  <text x="477" y="1010" font-size="34" fill="var(--fall)">FALL</text>
  <text x="477" y="1073" font-size="60" fill="var(--fall)">Q4 2018</text>

  <!-- winter -->
  <path d="M988 762 A44 44 0 0 1 937 815" fill="none" stroke="var(--winter)" stroke-width="3"/>
  <path d="M980 804 Q1000 845 1035 845 H1257" fill="none" stroke="var(--winter)" stroke-width="3"/>
  <circle cx="1257" cy="846" r="9" fill="var(--winter)"/>
  <circle cx="947" cy="771" r="26" fill="var(--winter)"/><circle cx="947" cy="771" r="11" fill="#fff"/>
  <g stroke="var(--winter)" stroke-width="6" stroke-linecap="round" fill="none">
    <path d="M1303 812v68M1274 829l58 34M1274 863l58 -34"/>
    <path d="M1294 818l9 8 9-8M1294 874l9-8 9 8M1278 840l12 3-3 12M1328 852l-12-3 3-12"/>
  </g>
  <text x="1055" y="830" font-size="34" fill="var(--winter)">WINTER</text>
  <text x="1055" y="898" font-size="60" fill="var(--winter)">Q1 2019</text>

  <!-- spring -->
  <path d="M1163 557 A44 44 0 0 1 1110 610" fill="none" stroke="var(--spring)" stroke-width="3"/>
  <path d="M1152 600 Q1185 641 1215 641 H1432" fill="none" stroke="var(--spring)" stroke-width="3"/>
  <circle cx="1432" cy="642" r="9" fill="var(--spring)"/>
  <circle cx="1120" cy="569" r="26" fill="var(--spring)"/><circle cx="1120" cy="569" r="11" fill="#fff"/>
  <g fill="var(--spring)">
    <circle cx="1481" cy="622" r="11"/><circle cx="1481" cy="662" r="11"/>
    <circle cx="1461" cy="642" r="11"/><circle cx="1501" cy="642" r="11"/>
    <circle cx="1467" cy="628" r="11"/><circle cx="1495" cy="628" r="11"/>
    <circle cx="1467" cy="656" r="11"/><circle cx="1495" cy="656" r="11"/>
    <circle cx="1481" cy="642" r="7" fill="#fff"/>
  </g>
  <text x="1227" y="620" font-size="34" fill="var(--spring)">SPRING</text>
  <text x="1227" y="690" font-size="60" fill="var(--spring)">Q2 2019</text>

  <!-- 2020 target -->
  <circle cx="1283" cy="373" r="48" fill="var(--spring)"/>
  <circle cx="1283" cy="373" r="34" fill="#fff"/>
  <circle cx="1283" cy="373" r="23" fill="var(--spring)"/>
  <circle cx="1283" cy="373" r="11" fill="#fff"/>
  <text x="1358" y="366" font-size="78" fill="var(--spring)">2020</text>
  <text x="1358" y="413" font-size="48" fill="var(--spring)">VALUE CREATION</text>

  <!-- phase timeline -->
  <line x1="145" y1="1245" x2="1640" y2="1245" stroke="#999" stroke-width="2" stroke-dasharray="2 10"/>
  <circle cx="145" cy="1245" r="9" fill="var(--summer)"/>
  <circle cx="1640" cy="1245" r="9" fill="var(--spring)"/>
</svg>

<div class="phase-row">
  <div class="pill assessment"><svg width="22" height="22" viewBox="0 0 22 22"><circle cx="11" cy="11" r="8" fill="none" stroke="#fff" stroke-width="2"/><circle cx="11" cy="11" r="4" fill="#fff"/></svg>ASSESSMENT</div>
  <div class="pill stabilize"><svg width="22" height="22" viewBox="0 0 22 22"><path d="M11 1 L14 6 L20 5 L17 11 L20 15 L13 15 L11 21 L9 15 L2 15 L5 11 L2 5 L8 6 Z" fill="#fff"/></svg>STABILIZE</div>
  <div class="pill stratactical"><svg width="22" height="22" viewBox="0 0 22 22"><path d="M11 1v20M2 6l18 10M2 16l18-10" stroke="#fff" stroke-width="2" stroke-linecap="round"/></svg>STRATACTICAL</div>
  <div class="pill strategic"><svg width="22" height="22" viewBox="0 0 22 22"><g fill="#fff"><circle cx="11" cy="4" r="4"/><circle cx="11" cy="18" r="4"/><circle cx="4" cy="11" r="4"/><circle cx="18" cy="11" r="4"/><circle cx="6" cy="6" r="4"/><circle cx="16" cy="6" r="4"/><circle cx="6" cy="16" r="4"/><circle cx="16" cy="16" r="4"/></g><circle cx="11" cy="11" r="2.5" fill="var(--spring)"/></svg>STRATEGIC</div>
</div>

<section class="column assessment">
  <h3>Marlowbend</h3>
  <ul class="group">
    <li><span>Transitions</span><ul class="items">
      <li>RO Transition from Reed &amp; Mira</li>
      <li>Start CR Office Initiative</li>
      <li>Tactical Ops transition from Reed</li>
      <li>Formalize Exec Team</li></ul></li>
    <li><span>Biz Architecture</span><ul class="items">
      <li>Independent Financial Audit</li>
      <li>Organizational Audit - Structure</li>
      <li>Organizational Audit - People</li>
      <li>XF Framework - ESU</li>
      <li>Defined Utilization, Realization, Availability</li></ul></li>
    <li><span>Strategy</span><ul class="items">
      <li>Effective Strategy Meeting</li>
      <li>Strategic Themes 2018 - 2020: Stablize, Accelerate, Surge</li>
      <li>Business Drivers: Drive Revenue, Improve Corvane Experience, Increase Brand Awareness</li></ul></li>
    <li><span>Sales</span><ul class="items">
      <li>Harrowgate Account Transition</li>
      <li>Fennick Account Transition</li>
      <li>2 year Managed Services Engagement Model</li></ul></li>
    <li><span>Revenue / EBITA</span><ul class="items"><li>TBD</li></ul></li>
  </ul>
  <h3 class="effectiveness">Effectiveness</h3>
  <ul class="group"><li><span style="font-weight:400">Storming</span></li></ul>
</section>

<section class="column stabilize">
  <h3>Marlowbend</h3>
  <ul class="group">
    <li><span>Biz Architecture</span><ul class="items">
      <li>XF Framework - Functional Meetings &amp; Scrum of Scrums</li>
      <li>Structured Reorg</li>
      <li>Implemented Reorg</li>
      <li>Quarterly Org Iteration cadence</li>
      <li>Defined Key Hire Plan</li>
      <li>CR Office Operational</li>
      <li>Time Accountability</li>
      <li>Tools ReConfig</li>
      <li>Org Structure v1</li></ul></li>
    <li><span>Strategy</span><ul class="items"><li>Internal QBR Accountability</li></ul></li>
    <li><span>Sales</span><ul class="items"><li>Calloway QBR</li><li>Harrowgate QBR</li></ul></li>
    <li><span>Revenue / EBITA</span><ul class="items"><li>TBD</li></ul></li>
  </ul>
  <h3 class="effectiveness">Effectiveness</h3>
  <ul class="group"><li><span style="font-weight:400">Activity</span></li></ul>
</section>

<section class="column stratactical">
  <h3>Marlowbend</h3>
  <ul class="group">
    <li><span>Biz Architecture</span><ul class="items">
      <li>XF Framework - Progress Demos</li>
      <li>Org Structure - COE's</li>
      <li>Stablize Accounting &amp; Finance</li>
      <li>Exec Hiring Process</li></ul></li>
    <li><span>Key Hires</span><ul class="items"><li>Controller</li><li>Director CX</li></ul></li>
    <li><span>Strategy</span><ul class="items">
      <li>Founders removed from front line activity</li>
      <li>Vantor QBR - Goal Setting &amp; Tracking</li>
      <li>Sales</li>
      <li>Fennick QBR</li>
      <li>Harrowgate QBR</li></ul></li>
    <li><span>Revenue / EBITA</span><ul class="items"><li>TBD</li></ul></li>
  </ul>
  <h3 class="effectiveness">Effectiveness</h3>
  <ul class="group"><li><span>Marlowbend</span></li></ul>
</section>

<section class="column strategic">
  <h3>Marlowbend</h3>
  <ul class="group">
    <li><span>Biz Architecture</span><ul class="items">
      <li>Tiered Pricing Pre-Paid Engagement Model</li>
      <li>XF Framework - Ideation Board</li>
      <li>Consulting Levels &amp; Salary Bands</li>
      <li>Roles &amp; Responsibilities</li></ul></li>
    <li><span>Key Hires</span><ul class="items">
      <li>Interim HR</li>
      <li>Provisional Client Partner</li>
      <li>Acting Director 1</li>
      <li>Acting Director 2</li>
      <li>Client Partner 1</li>
      <li>Sales Exec 1</li></ul></li>
    <li><span>Sales</span><ul class="items">
      <li>Opened Brightwell Door</li>
      <li>Flipped focus from operationaly run company to sales/marketing driven org</li>
      <li>Kestrel Direct</li></ul></li>
    <li><span>Revenue / EBITA</span><ul class="items"><li>TBD</li></ul></li>
  </ul>
  <h3 class="effectiveness">Effectiveness</h3>
  <ul class="group"><li><span>Outcomes</span></li></ul>
</section>
</body>
</html>
```